Water ATM Card

Need a design for water ATM cards. Size of card is 3.375 x 2.125 inch
On the Front include the Cedar hollow Logo.
Bottom right corner should have Price $100
On the Back
This card is to be used to access water refills at any Cedar Hollow Water Vending Machines.
Please contact (869) 418 2930 or (869) 534 1276 or email clearflowbox@mailvista.example for any assistance or recharging of card.

```html
<!DOCTYPE html>
<html lang="en">
<head>
<meta charset="utf-8">
<title>Cedar Hollow Water Card</title>
<link href="https://fonts.googleapis.com/css2?family=Montserrat:wght@400;500;700;800&display=swap" rel="stylesheet">
<style>
  :root {
    --stage: #b3b3b3;
    --paper: #ffffff;
    --navy: #2b4390;
    --blue: #2f5db0;
    --blue-light: #3a6aa8;
    --green: #2e9e3e;
    --ink: #1d1d1d;
  }
  * { box-sizing: border-box; margin: 0; padding: 0; }
  html, body { width: 1200px; height: 900px; overflow: hidden; }
  body {
    background: var(--stage);
    font-family: "Montserrat", sans-serif;
    position: relative;
  }
  .card {
    position: absolute;
    width: 560px;
    height: 352px;
    border-radius: 2px;
    box-shadow: 0 10px 24px rgba(0,0,0,.25);
    overflow: hidden;
  }
  /* Front */
  .card-front { left: 50px; top: 90px; background: var(--paper); }
  .card-front .edge-band {
    position: absolute; left: 0; right: 0; bottom: 0; height: 14px;
    background: var(--navy);
  }
  .brand-front {
    position: absolute; right: 40px; top: 40px;
    display: flex; align-items: center; gap: 10px;
    font-weight: 800; font-size: 26px; letter-spacing: 1px;
    color: var(--blue); text-transform: uppercase;
  }
  .brand-dot { width: 14px; height: 14px; border-radius: 50%; background: var(--blue); }
  .holder { position: absolute; left: 30px; top: 112px; }
  .holder-name {
    font-weight: 800; font-size: 20px; color: var(--navy);
    text-transform: uppercase; letter-spacing: .5px;
  }
  .holder-role { font-size: 12px; color: var(--ink); margin-top: 4px; letter-spacing: .5px; }
  .divider {
    position: absolute; left: 30px; right: 30px; top: 166px;
    height: 1.5px; background: var(--blue);
  }
  .contact-list {
    position: absolute; left: 30px; top: 190px;
    list-style: none; font-size: 13px; color: var(--ink);
  }
  .contact-list li { display: flex; align-items: center; gap: 9px; height: 24px; }
  .contact-list svg { width: 14px; height: 14px; flex: none; }
  .address {
    position: absolute; right: 30px; top: 192px;
    font-size: 13px; line-height: 1.45; color: var(--ink); text-align: right;
  }
  .price {
    position: absolute; right: 30px; bottom: 36px;
    font-weight: 800; font-size: 30px; color: var(--green);
  }
  /* Back */
  .card-back {
    left: 590px; top: 450px;
    background: linear-gradient(135deg, var(--blue-light) 0%, var(--navy) 75%);
    color: var(--paper);
  }
  .brand-back {
    position: absolute; left: 0; right: 0; top: 84px;
    display: flex; justify-content: center; align-items: center; gap: 14px;
    font-weight: 800; font-size: 40px; letter-spacing: 2px; text-transform: uppercase;
  }
  .brand-back .brand-dot { width: 20px; height: 20px; background: var(--paper); }
  .back-copy {
    position: absolute; left: 40px; right: 40px; bottom: 40px;
    text-align: center; font-size: 13px; line-height: 1.55; letter-spacing: .2px;
  }
  .back-copy p + p { margin-top: 10px; }
</style>
</head>
<body>
  <section class="card card-front">
    <div class="brand-front"><span class="brand-dot"></span>Cedar Hollow</div>
    <div class="holder">
      <div class="holder-name">Dara Whitlock</div>
      <div class="holder-role">OWER</div>
    </div>
    <div class="divider"></div>
    <ul class="contact-list">
      <li>
        <svg viewBox="0 0 16 16"><path fill="#2b4390" d="M3 1l3 3-1.5 2a9 9 0 0 0 5.5 5.5L12 10l3 3-2 2C7 15 1 9 1 3z"/></svg>
        (869) 418 2930
      </li>
      <li>
        <svg viewBox="0 0 16 16"><rect x="4" y="1" width="8" height="14" rx="1.5" fill="none" stroke="#2b4390" stroke-width="1.6"/><circle cx="8" cy="12.5" r="1" fill="#2b4390"/></svg>
        (869) 534 1276
      </li>
      <li>
        <svg viewBox="0 0 16 16"><rect x="1" y="3" width="14" height="10" rx="1" fill="#2b4390"/><path d="M1.5 3.5L8 9l6.5-5.5" fill="none" stroke="#fff" stroke-width="1.2"/></svg>
        clearflowbox@mailvista.example
      </li>
      <li>
        <svg viewBox="0 0 16 16"><circle cx="8" cy="8" r="6.5" fill="none" stroke="#2b4390" stroke-width="1.6"/><path d="M1.5 8h13M8 1.5c-3 3.5-3 9.5 0 13M8 1.5c3 3.5 3 9.5 0 13" fill="none" stroke="#2b4390" stroke-width="1.2"/></svg>
        www.cedarhollowwater.example
      </li>
    </ul>
    <div class="address">480 Fernbrook Lane, Ste<br>12 Millbrook, TN 37999</div>
    <div class="price">Price $100</div>
    <div class="edge-band"></div>
  </section>

  <section class="card card-back">
    <div class="brand-back"><span class="brand-dot"></span>Cedar Hollow</div>
    <div class="back-copy">
      <p>This card is to be used to access water refills at any Cedar Hollow Water Vending Machines.</p>
      <p>Please contact (869) 418 2930 or (869) 534 1276 or email clearflowbox@mailvista.example for any assistance or recharging of card.</p>
    </div>
  </section>
</body>
</html>
```